Seeking funky, innovative business cards

I am looking to refresh our current business cards to something more engaging, visual and impactful. We are a management consultancy firm, see website (www.larkstone-partners.com.au). I've included our colour scheme, sample of the slides we use and our old business cards. We would like our cards to have icons. The card should display:- Name- Title- Mobile number- Address- Email address- Website - Company logo- Our purpose statement "we shape the finest workplaces in the world"

Contact Information for Business Card

Brennan Ulfsson
Consultant
0468 927 341
Level 3, 218 Wexley Street, Melbourne 3000
brennan@larkstone-partners.com.au
www.larkstone-partners.com.au

Purpose statement "we shape the finest workplaces in the world"
LOGO available in google images

Font styles to use
Other font styles liked:
• Open Sans Light, Bebas Neue (open to other cool foints)

Colors
ffc214
5c5c5c
f5f5f5
fefefe

Requirements
Must have
• - Name
• - Title
• - Mobile number
• - Address
• - Email address
• - Website
• - Company logo
• - Our purpose statement "we shape the finest workplaces in the world"
Nice to have
• - Icons
• - Colour (see our colour scheme"

```html
<!DOCTYPE html>
<html lang="en">
<head>
<meta charset="utf-8">
<title>Larkstone Partners – Business Card</title>
<link href="https://fonts.googleapis.com/css2?family=Roboto:ital,wght@0,300;0,400;1,500&display=swap" rel="stylesheet">
<style>
  :root {
    --backdrop: #b9b9b9;
    --card-white: #fefefe;
    --brand-yellow: #ffc214;
    --accent-orange: #f6a623;
    --text-grey: #5c5c5c;
    --text-dark: #3a3a3a;
  }
  * { margin: 0; padding: 0; box-sizing: border-box; }
  html, body { width: 1200px; height: 1200px; overflow: hidden; }
  body {
    background: var(--backdrop);
    font-family: "Roboto", Arial, sans-serif;
    position: relative;
  }
  .card {
    position: absolute;
    left: 218px;
    width: 800px;
    height: 456px;
  }
  .card--front { top: 116px; background: var(--card-white); }
  .card--back { top: 638px; background: var(--brand-yellow); }

  .wordmark {
    position: absolute;
    display: flex;
    align-items: center;
    gap: 14px;
    font-weight: 300;
    white-space: nowrap;
  }
  .wordmark__dot { border-radius: 50%; flex: none; }
  .card--front .wordmark { left: 56px; top: 98px; font-size: 46px; color: var(--text-grey); }
  .card--front .wordmark__dot { width: 16px; height: 16px; background: var(--brand-yellow); }
  .card--back .wordmark {
    left: 0; right: 0; top: 190px; justify-content: center;
    font-size: 60px; color: var(--card-white);
  }
  .card--back .wordmark__dot { width: 20px; height: 20px; background: var(--card-white); }

  .address {
    position: absolute; left: 56px; top: 278px;
    font-size: 19px; line-height: 24px; color: var(--text-grey);
  }
  .contacts {
    position: absolute; left: 56px; top: 339px;
    list-style: none; font-size: 19px; color: var(--text-grey);
  }
  .contacts li { display: flex; align-items: center; height: 26px; }
  .contacts svg { width: 18px; height: 18px; margin-right: 12px; flex: none; }

  .person {
    position: absolute; right: 54px; top: 316px; text-align: right;
  }
  .person__name { font-size: 30px; color: var(--accent-orange); line-height: 36px; }
  .person__title { font-size: 20px; color: var(--text-dark); line-height: 24px; }

  .purpose {
    position: absolute; left: 0; right: 0; top: 382px;
    text-align: center; font-style: italic; font-weight: 500; font-size: 21px;
    color: var(--card-white);
  }
</style>
</head>
<body>
  <section class="card card--front">
    <div class="wordmark"><span class="wordmark__dot"></span>Larkstone Partners</div>

    <p class="address">Level 3, 218 Wexley Street,<br>Melbourne 3000</p>
    <ul class="contacts">
      <li>
        <svg viewBox="0 0 24 24" aria-hidden="true"><path fill="#f6a623" d="M6.6 10.8a15.1 15.1 0 0 0 6.6 6.6l2.2-2.2c.3-.3.7-.4 1-.2 1.1.4 2.3.6 3.6.6.6 0 1 .4 1 1V20c0 .6-.4 1-1 1A17 17 0 0 1 3 4c0-.6.4-1 1-1h3.5c.6 0 1 .4 1 1 0 1.3.2 2.5.6 3.6.1.3 0 .7-.2 1z"/></svg>
        0468 927 341
      </li>
      <li>
        <svg viewBox="0 0 24 24" aria-hidden="true"><rect x="3" y="6" width="18" height="12" fill="none" stroke="#f6a623" stroke-width="2"/><path d="M3 6l9 7 9-7" fill="none" stroke="#f6a623" stroke-width="2"/></svg>
        brennan@larkstone-partners.com.au
      </li>
      <li>
        <svg viewBox="0 0 24 24" aria-hidden="true"><circle cx="12" cy="12" r="9" fill="#f6a623"/><path d="M8 7c2 1 1 3 3 3s1 3-1 4M15 15c1-1 3 0 3-2" fill="none" stroke="#fff" stroke-width="1.6"/></svg>
        www.larkstone-partners.com.au
      </li>
    </ul>

    <div class="person">
      <p class="person__name">Brennan Ulfsson</p>
      <p class="person__title">Consultant</p>
    </div>
  </section>

  <section class="card card--back">
    <div class="wordmark"><span class="wordmark__dot"></span>Larkstone Partners</div>
    <p class="purpose">we shape the finest workplaces in the world</p>
  </section>
</body>
</html>
```